Site for entrepreneurs/small businesses needs Logo, Homepage

Looking for a logo, either an icon, or stylized text, or a combination of both, and a home page design which fits with it. The logo will be for use on the public website as well as for printed collateral (business cards, post cards, brochures and various other marketing materials).

The site is called Orbitwell (Orbitwell.example). This is to be a national, and eventually an international brand. The new service will provide an easy-to-use platform for entrepreneurs to build their business and web presence together in an integrated way which allows them to focus on their core competency.

The site/service will be dead-simple to use, A/B/C, 1/2/3. We will want some sort of "Get started for FREE" promotional space to collect the person's email address with multiple points of interest which guide the user back to this one call to action: sign up for free. We will feature editorial/blog stories, customer testimonials, and present several key features the the reader just can't live without if they are starting a new business.

Criteria:
* Refer to our comparable sites/logos in the design document attached
* Incorporate our color scheme (but complementary colors welcome)
* No Serif fonts!
* No photo-realistic elements for logo
* Logo must present well in gray scale and/or black/white (for printed materials)
* Strokes/borders that are wider to promote simplicity (vs. thin/precise lines which promote technical complexity)

Inspirations:
* Creative/Custom (but legible) fonts
* Excitement, energetic, jumping for joy
* Karate / Ninja / Power / Precision
* Dance Moves
* Regional influences: California, Silicon Valley, West Coast, Surf City, Beaches, Sunset
* Simple/easy, no-brainer solutions

Target Market(s)

Small Businesses / Entrepreneurs

Logo Text

Orbitwell or Orbitwell.example

Number of Pages Required

1 page

Font styles to use
Sans Serif
Decorative

Requirements
Must have
• See the attached style guide (PDF)

```html
<!DOCTYPE html>
<html lang="en">
<head>
<meta charset="utf-8">
<title>Orbitwell — Build your business and web presence together</title>
<link href="https://fonts.googleapis.com/css2?family=Mulish:wght@400;600;700;800&display=swap" rel="stylesheet">
<style>
:root{
  --purple:#5b1aa0;
  --purple-deep:#3a0d78;
  --magenta:#8a2bbf;
  --orange:#f7931e;
  --ink:#2b2b3a;
  --muted:#8a8a99;
  --line:#e4e4ec;
  --white:#ffffff;
}
*{box-sizing:border-box;margin:0;padding:0}
html,body{width:1200px;height:4336px;overflow:hidden}
body{position:relative;background:var(--white);font-family:"Mulish",Arial,sans-serif;color:var(--ink)}
.abs{position:absolute}
.backdrop{position:absolute;left:0;top:0;width:1200px;height:4336px}
.btn{position:absolute;background:var(--orange);color:var(--white);font-weight:700;font-size:15px;border-radius:22px;display:flex;align-items:center;justify-content:center;text-transform:uppercase;letter-spacing:.5px;box-shadow:0 6px 14px rgba(247,147,30,.35)}
.brand{position:absolute;display:flex;align-items:center;gap:10px;font-weight:800;font-size:26px;z-index:2}
.brand-dot{width:22px;height:22px;border-radius:50%;background:var(--orange)}
.nav{position:absolute;top:44px;right:40px;display:flex;gap:30px;color:var(--white);font-size:15px;font-weight:600;z-index:2}
.hero-title{left:100px;top:210px;color:var(--white);font-size:52px;font-weight:800;z-index:2}
.hero-copy{left:100px;top:296px;width:480px;color:var(--white);font-size:20px;line-height:1.5;z-index:2}
.art{position:absolute;border-radius:6px}
.hero-art{left:620px;top:90px;width:520px;height:620px;border-radius:50%;background:radial-gradient(ellipse at 50% 50%,rgba(120,60,190,.55) 0%,rgba(74,22,144,.25) 55%,rgba(74,22,144,0) 72%)}
.signup{left:288px;top:528px;width:744px;height:292px;background:var(--white);border-radius:22px;box-shadow:0 12px 40px rgba(40,10,90,.18);z-index:3}
.signup h2{position:absolute;top:48px;width:100%;text-align:center;font-size:40px;font-weight:700}
.signup p{position:absolute;top:114px;width:100%;text-align:center;font-size:12px;color:var(--muted);letter-spacing:.8px;text-transform:uppercase}
.field{position:absolute;border:1px solid var(--line);background:var(--white);font-size:14px;color:var(--muted);display:flex;align-items:center;padding-left:20px}
.feature-card{position:absolute;top:960px;width:300px;height:420px;background:var(--white);border:1px solid var(--line);box-shadow:0 10px 30px rgba(40,10,90,.15);text-align:center}
.feature-card .icon{width:72px;height:72px;border-radius:50%;margin:56px auto 20px;background:linear-gradient(135deg,#e74c3c,#3c7fd6)}
.feature-card h3{font-size:24px;font-weight:700;line-height:1.2;padding:0 24px}
.feature-card p{font-size:13px;color:var(--muted);line-height:1.7;padding:18px 44px 0}
.feature-card .btn{left:96px;bottom:34px;width:108px;height:40px;font-size:13px}
.section-title{position:absolute;font-size:44px;font-weight:600}
.body-copy{position:absolute;font-size:15px;color:var(--muted);line-height:1.8}
.checks{position:absolute;left:572px;top:2150px;list-style:none;font-size:15px;color:var(--muted);line-height:2.1}
.checks li{display:flex;align-items:center;gap:14px}
.checks svg{flex:none}
.center{width:1200px;text-align:center;left:0}
.quote-card{position:absolute;top:2620px;width:430px;height:290px;background:var(--white);box-shadow:0 10px 30px rgba(40,10,90,.12);padding:40px 40px 0 70px}
.quote-mark{position:absolute;left:22px;top:14px;color:var(--purple);font-size:72px;font-weight:800;line-height:1}
.quote-card p{font-size:14px;color:var(--muted);line-height:1.8}
.person{position:absolute;left:70px;bottom:34px;display:flex;align-items:center;gap:16px}
.avatar{width:52px;height:52px;border-radius:50%;background:linear-gradient(135deg,#c98b6a,#6a4a3a)}
.person b{display:block;font-size:14px;color:var(--purple)}
.person span{font-size:12px;color:var(--muted)}
.dots{position:absolute;top:2974px;left:576px;display:flex;gap:10px}
.dots i{width:10px;height:10px;border-radius:50%;background:#cfc8dd}
.dots i:first-child{background:var(--purple)}
.blog-card{position:absolute;top:3260px;width:320px;height:400px;background:var(--white);box-shadow:0 10px 30px rgba(40,10,90,.15)}
.blog-card .thumb{height:200px}
.blog-card p{padding:26px 26px 0;font-size:14px;color:var(--muted);line-height:1.7}
.blog-card .person{left:26px;bottom:26px;gap:10px}
.blog-card .avatar{width:38px;height:38px}
.blog-card .person b{font-size:12px;color:var(--ink)}
.blog-card .btn{right:22px;bottom:28px;width:112px;height:36px;font-size:12px;text-transform:none}
.rule{position:absolute;left:100px;top:3780px;width:1000px;height:1px;background:var(--line)}
.footer-links{position:absolute;top:4072px;font-size:14px;line-height:1.9;color:var(--ink)}
.social{position:absolute;top:4100px;left:880px;display:flex;gap:14px}
.social i{width:36px;height:36px;border-radius:50%;border:2px solid var(--purple);background:var(--white)}
.copyright{position:absolute;top:4292px;width:1200px;text-align:center;font-size:12px;color:var(--white)}
</style>
</head>
<body>

<svg class="backdrop" viewBox="0 0 1200 4336" aria-hidden="true">
  <defs>
    <linearGradient id="grad" x1="0" y1="0" x2="1" y2="1">
      <stop offset="0" stop-color="#7a22b3"/>
      <stop offset="1" stop-color="#3a0d78"/>
    </linearGradient>
  </defs>
  <polygon points="0,0 1200,0 1200,820 0,740" fill="url(#grad)"/>
  <polygon points="0,800 240,980 150,1200 0,1330" fill="url(#grad)"/>
  <polygon points="1200,1160 1060,1500 980,1960 1200,1990" fill="url(#grad)"/>
  <polygon points="0,1960 130,2040 170,2480 0,2640" fill="url(#grad)"/>
  <polygon points="1200,3450 1200,4336 1110,4336 1160,3900" fill="url(#grad)"/>
  <polygon points="0,4170 0,4336 1000,4336 1050,4260" fill="url(#grad)"/>
</svg>

<!-- Header -->
<div class="brand" style="left:40px;top:28px;color:var(--white)"><span class="brand-dot"></span>Orbitwell</div>
<nav class="nav"><span>Home</span><span>About Us</span><span>Services</span><span>Who We Are</span><span>Our Solution</span><span>Contact Us</span></nav>

<div class="art hero-art" role="img" aria-label="Illustration of a person launching on a large rocket with small rockets and coins"></div>
<h1 class="abs hero-title">Orbitwell</h1>
<p class="abs hero-copy">At vero eos et accusamus et iusto odio dignissimos ducimus qui blanditiis praese voluptatum deleniti atque corrupti</p>
<div class="btn" style="left:100px;top:410px;width:150px;height:44px;z-index:2">Learn More</div>

<!-- Sign up -->
<section class="abs signup">
  <h2>Get started for FREE</h2>
  <p>Sed ut perspiciatis unde omnis iste natus error sit voluptatem</p>
  <div class="field" style="left:84px;top:200px;width:420px;height:48px">Enter Your Email Address</div>
  <div class="btn" style="left:504px;top:200px;width:160px;height:48px;border-radius:0;font-size:13px">Sign Up For Free</div>
</section>

<!-- Feature cards -->
<article class="feature-card" style="left:96px"><div class="icon" role="img" aria-label="Network icon"></div><h3>At vero eos et accusamus et iusto</h3><p>Sed ut perspiciatis unde omnis iste natus error sit voluptatem accusantium doloremque laudant.</p><div class="btn">Read More</div></article>
<article class="feature-card" style="left:452px"><div class="icon" role="img" aria-label="Growth icon" style="background:linear-gradient(135deg,#3fb36b,#f0a22b)"></div><h3>At vero eos et accusamus et iusto</h3><p>Sed ut perspiciatis unde omnis iste natus error sit voluptatem accusantium doloremque laudant.</p><div class="btn">Read More</div></article>
<article class="feature-card" style="left:808px"><div class="icon" role="img" aria-label="Global business icon" style="background:linear-gradient(135deg,#2f6f8f,#3a3a4a)"></div><h3>At vero eos et accusamus et iusto</h3><p>Sed ut perspiciatis unde omnis iste natus error sit voluptatem accusantium doloremque laudant.</p><div class="btn">Read More</div></article>

<!-- Who we are -->
<h2 class="section-title" style="left:100px;top:1520px">Who We Are</h2>
<p class="body-copy" style="left:100px;top:1596px;width:440px">At vero eos et accusamus et iusto odio dignissimos ducimus qui blanditiis praesentium voluptatum deleniti atque corrupti quos dolores et quas molestias excepturi sint occaecati cupiditate non provident, similique sunt in culpa qui officia deserunt mollitia animi, id est laborum et dolorum fuga. Et harum quidem rerum facilis est et expedita distinctio nam libero tempore cum soluta.</p>
<div class="btn" style="left:100px;top:1832px;width:140px;height:44px;font-size:13px">Read More</div>
<div class="art" role="img" aria-label="Isometric illustration of a team meeting around a conference table" style="left:620px;top:1580px;width:500px;height:260px;background:linear-gradient(135deg,#eef0f4,#c9ccd6)"></div>

<!-- Key features -->
<div class="art" role="img" aria-label="Illustration of a businessman arranging connected circuit lines" style="left:112px;top:2040px;width:390px;height:300px;background:linear-gradient(135deg,#f1eff4,#d9d4e2)"></div>
<h2 class="section-title" style="left:572px;top:2070px">Key Features</h2>
<ul class="checks">
  <li><svg width="16" height="16" viewBox="0 0 16 16"><path d="M2 8l4 4 8-9" fill="none" stroke="#f7931e" stroke-width="2.5"/></svg>At vero eos et accusamus et iusto odio dignissimos ducimus</li>
  <li><svg width="16" height="16" viewBox="0 0 16 16"><path d="M2 8l4 4 8-9" fill="none" stroke="#f7931e" stroke-width="2.5"/></svg>Praesentium voluptatum deleniti atque corrupti quos dolores</li>
  <li><svg width="16" height="16" viewBox="0 0 16 16"><path d="M2 8l4 4 8-9" fill="none" stroke="#f7931e" stroke-width="2.5"/></svg>Nam libero tempore cum soluta nobis est eligendi</li>
  <li><svg width="16" height="16" viewBox="0 0 16 16"><path d="M2 8l4 4 8-9" fill="none" stroke="#f7931e" stroke-width="2.5"/></svg>Temporibus autem quibusdam et aut officiis debitis aut rerum</li>
  <li><svg width="16" height="16" viewBox="0 0 16 16"><path d="M2 8l4 4 8-9" fill="none" stroke="#f7931e" stroke-width="2.5"/></svg>Et harum quidem rerum facilis est et expedita distinctio</li>
  <li><svg width="16" height="16" viewBox="0 0 16 16"><path d="M2 8l4 4 8-9" fill="none" stroke="#f7931e" stroke-width="2.5"/></svg>Sed ut perspiciatis unde omnis iste natus error sit voluptatem</li>
</ul>
<div class="btn" style="left:572px;top:2356px;width:140px;height:44px;font-size:13px">Read More</div>

<!-- Testimonials -->
<h2 class="section-title center" style="top:2510px;font-size:38px">Customer Testimonials</h2>
<article class="quote-card" style="left:170px"><span class="quote-mark">“</span><p>At harum quidem rerum facilis est et expedita distinctio. Nam libero tempore, cum soluta nobis est eligendi optio cumque nihil impedit quo minus id quod maxime placeat facere possimus.</p><div class="person"><div class="avatar" role="img" aria-label="Portrait photo of the customer"></div><div><b>Tessa Lind</b><span>Founder, Bright Lane Studio</span></div></div></article>
<article class="quote-card" style="left:620px"><span class="quote-mark">“</span><p>At harum quidem rerum facilis est et expedita distinctio. Nam libero tempore, cum soluta nobis est eligendi optio cumque nihil impedit quo minus id quod maxime placeat facere possimus.</p><div class="person"><div class="avatar" role="img" aria-label="Portrait photo of the customer"></div><div><b>Tessa Lind</b><span>Founder, Bright Lane Studio</span></div></div></article>
<div class="dots"><i></i><i></i><i></i></div>

<!-- Blog -->
<h2 class="section-title center" style="top:3100px">Our Blog</h2>
<p class="abs center" style="top:3174px;font-size:12px;color:var(--muted);letter-spacing:.8px;text-transform:uppercase">Sed ut perspiciatis unde omnis iste natus error sit voluptatem</p>
<article class="blog-card" style="left:100px"><div class="thumb" role="img" aria-label="Illustration of a presenter at a desk" style="background:linear-gradient(135deg,#2fb59a,#1c8f7a)"></div><p>Lorem ipsum dolor sit amet, consectetur adipiscing elit, sed do eiusmod.</p><div class="person"><div class="avatar" role="img" aria-label="Author photo"></div><b>Owen Pryce</b></div><div class="btn">View Details</div></article>
<article class="blog-card" style="left:440px"><div class="thumb" role="img" aria-label="Illustration of analytics charts on a screen" style="background:linear-gradient(135deg,#e8eef7,#9fb7d8)"></div><p>Lorem ipsum dolor sit amet, consectetur adipiscing elit, sed do eiusmod.</p><div class="person"><div class="avatar" role="img" aria-label="Author photo"></div><b>Owen Pryce</b></div><div class="btn">View Details</div></article>
<article class="blog-card" style="left:780px"><div class="thumb" role="img" aria-label="Photo of a team celebrating in an office" style="background:linear-gradient(135deg,#e9e3dc,#b8a99a)"></div><p>Lorem ipsum dolor sit amet, consectetur adipiscing elit, sed do eiusmod.</p><div class="person"><div class="avatar" role="img" aria-label="Author photo"></div><b>Owen Pryce</b></div><div class="btn">View Details</div></article>

<!-- Newsletter -->
<div class="rule"></div>
<p class="abs" style="left:100px;top:3852px;width:460px;font-size:22px;line-height:1.45">Let's talk about how can help you better understand your users.</p>
<div class="field" style="left:652px;top:3860px;width:412px;height:52px;border-radius:26px;box-shadow:0 6px 18px rgba(40,10,90,.12)">Enter Your Email Address
  <svg style="position:absolute;right:22px" width="26" height="14" viewBox="0 0 26 14"><path d="M0 7h22M16 1l6 6-6 6" fill="none" stroke="#5b1aa0" stroke-width="2.5"/></svg>
</div>

<!-- Footer -->
<div class="brand" style="left:100px;top:4090px;color:var(--purple)"><span class="brand-dot"></span>Orbitwell</div>
<div class="footer-links" style="left:412px"><div>About</div><div>Blog</div><div>Careers</div><div>Terms Of Service</div></div>
<div class="footer-links" style="left:592px"><div>Faq</div><div>Privacy policy</div><div>Sitemap</div></div>
<div class="social"><i></i><i></i><i></i><i></i></div>
<div class="copyright">© 2018 Copyright Orbitwell All Rights Reserved</div>

</body>
</html>
```